Company identity deisgn should support 2 languages

I would like to get our company identity design
This includes the following only
Business Cards 2 languages Arabic and English
Email signature
Letterhead
Linkedin profile images
Attached is the logo in Ai format

Requirements
Must have
• For business card
Must have
Name and Adrees in arabic
Name and Address in english
You might use both side of the card
Should not have
• Any pictures other than the logo

```html
<!DOCTYPE html>
<html lang="en">
<head>
<meta charset="utf-8">
<title>Cognitive Logic Systems – Business Card</title>
<link rel="stylesheet" href="https://fonts.googleapis.com/css2?family=Montserrat:wght@400;600;700&family=Roboto:wght@400;500;700&family=Cairo:wght@400;600&display=swap">
<style>
  :root {
    --brand-blue: #1f73c4;
    --paper: #f4f4f4;
    --card-white: #f9f9f9;
    --ink: #555b61;
    --ink-soft: #8a9096;
    --backdrop: #e9e7e4;
  }
  * { box-sizing: border-box; margin: 0; padding: 0; }
  html, body { width: 1200px; height: 960px; overflow: hidden; background: var(--backdrop); }
  .stage { position: relative; width: 1200px; height: 960px; }

  .card {
    position: absolute;
    width: 630px;
    height: 360px;
    border-radius: 4px;
    box-shadow: 0 10px 24px rgba(0,0,0,0.12), 0 2px 4px rgba(0,0,0,0.08);
    overflow: hidden;
  }

  /* Back side */
  .card-back { left: 60px; top: 70px; background: var(--brand-blue); color: #fff; }
  .card-back .wordmark {
    position: absolute; left: 0; right: 0; top: 130px;
    display: flex; align-items: center; justify-content: center; gap: 14px;
  }
  .wordmark .dot { width: 18px; height: 18px; border-radius: 50%; background: currentColor; flex: none; }
  .wordmark .name {
    font-family: "Montserrat", sans-serif; font-weight: 600;
    font-size: 26px; letter-spacing: 1.5px; text-transform: uppercase;
  }
  .card-back .website {
    position: absolute; left: 0; right: 0; bottom: 64px; text-align: center;
    font-family: "Montserrat", sans-serif; font-size: 16px; letter-spacing: 2px;
  }

  /* Front side */
  .card-front { left: 510px; top: 530px; background: var(--card-white); color: var(--ink); }
  .card-front .wordmark {
    position: absolute; right: 40px; top: 44px;
    display: flex; align-items: center; gap: 12px; color: var(--brand-blue);
  }
  .card-front .wordmark .name { font-size: 22px; }
  .card-front .edge-mark {
    position: absolute; left: 0; top: 176px; width: 22px; height: 40px; background: var(--brand-blue);
  }
  .holder { position: absolute; left: 46px; top: 120px; }
  .holder .name-line {
    font-family: "Roboto", sans-serif; font-weight: 700; font-size: 22px;
    color: var(--brand-blue); text-transform: uppercase; white-space: nowrap;
  }
  .holder .name-line .ar { font-family: "Cairo", sans-serif; font-weight: 600; text-transform: none; font-size: 22px; }
  .holder .role { font-family: "Roboto", sans-serif; font-weight: 500; font-size: 15px; color: var(--ink); margin-top: 2px; }
  .address { position: absolute; left: 46px; top: 220px; font-family: "Roboto", sans-serif; font-size: 16px; line-height: 1.45; color: var(--ink); }
  .address .ar { font-family: "Cairo", sans-serif; direction: rtl; text-align: left; unicode-bidi: plaintext; line-height: 1.55; }
  .contacts {
    position: absolute; right: 40px; top: 230px; list-style: none;
    font-family: "Roboto", sans-serif; font-size: 15px; color: var(--ink); line-height: 1.7;
  }
  .contacts li { display: flex; align-items: center; gap: 8px; }
  .contacts svg { width: 14px; height: 14px; flex: none; fill: var(--brand-blue); }
</style>
</head>
<body>
<main class="stage">

  <section class="card card-back" aria-label="Business card, back">
    <div class="wordmark">
      <span class="dot"></span>
      <span class="name">Cognitive Logic Systems</span>
    </div>
    <p class="website">www.cognilogicweb.com</p>
  </section>

  <section class="card card-front" aria-label="Business card, front">
    <div class="wordmark">
      <span class="dot"></span>
      <span class="name">Cognitive Logic Systems</span>
    </div>

    <span class="edge-mark"></span>

    <div class="holder">
      <p class="name-line">Daniel Hartwell <span class="ar" dir="rtl">(دانيال هارتويل)</span></p>
      <p class="role">Managing Director</p>
    </div>

    <div class="address">
      <p>42 Maple Ridge Rd, Vernon</p>
      <p>B.C. Canada V2X 5K7</p>
      <p class="ar" dir="rtl">٤٢ طريق ميبل ريدج، فيرنون</p>
      <p class="ar" dir="rtl">كولومبيا البريطانية، كندا V2X 5K7</p>
    </div>

    <ul class="contacts">
      <li>
        <svg viewBox="0 0 24 24" aria-hidden="true"><path d="M6.6 10.8a15.1 15.1 0 0 0 6.6 6.6l2.2-2.2a1 1 0 0 1 1-.25 11.4 11.4 0 0 0 3.6.57 1 1 0 0 1 1 1V20a1 1 0 0 1-1 1A17 17 0 0 1 3 4a1 1 0 0 1 1-1h3.5a1 1 0 0 1 1 1c0 1.25.2 2.45.57 3.57a1 1 0 0 1-.25 1z"/></svg>
        555.210.4477
      </li>
      <li>
        <svg viewBox="0 0 24 24" aria-hidden="true"><path d="M2 5h20v14H2zm2 2v.5l8 5 8-5V7l-8 5z"/></svg>
        info@cognilogicmail.com
      </li>
      <li>
        <svg viewBox="0 0 24 24" aria-hidden="true"><circle cx="12" cy="12" r="10"/></svg>
        www.cognilogicweb.com
      </li>
    </ul>
  </section>

</main>
</body>
</html>
```